Venture 482 - Lumora Book Cover

I am looking for a Lumora book cover for my book about "Venture 482".
The Book is Titled:
Venture 482 Ascended
Shaping Outcomes: Paths To Unlocking Cosmic Truths
Author is Dorian Pell
Here is a book description that may help you understand more about it:
Inspired by the genius of Edwin Marlowe, this comprehensive guide delves into the ancient wisdom and cutting-edge science behind the 482 method, a powerful tool for manifesting your desires. Whether you're seeking personal growth, financial success, or spiritual enlightenment, this book provides advanced techniques and methods to transform your dreams into reality.
Any questions please ask.
Thanks
Owen

```html
<!DOCTYPE html>
<html lang="en">
<head>
<meta charset="utf-8">
<title>Venture 482 Ascended — Dorian Pell</title>
<link rel="stylesheet" href="https://fonts.googleapis.com/css2?family=Cinzel:wght@400;500&family=Cormorant+Garamond:wght@500&family=Tinos&display=swap">
<style>
  :root {
    --ink-cream: #f7ece0;
    --ink-shadow: #1a0f22;
    --space-deep: #0b0a24;
    --space-indigo: #2a2170;
    --glow-violet: #8a4fc0;
    --glow-pink: #e07ac8;
  }
  * { margin: 0; padding: 0; box-sizing: border-box; }
  html, body {
    width: 805px; height: 1200px; overflow: hidden;
    background: var(--space-deep);
  }
  .cover {
    position: relative;
    width: 805px; height: 1200px;
    overflow: hidden;
    color: var(--ink-cream);
  }
  .cover-art {
    position: absolute; inset: 0;
    width: 805px; height: 1200px;
  }
  .title-line, .title-number, .title-tag,
  .subtitle-lead, .subtitle-body, .author {
    position: absolute; left: 0; width: 100%;
    text-align: center; white-space: nowrap;
  }
  .title-line {
    top: 62px;
    font-family: "Cinzel", serif;
    font-weight: 400;
    font-size: 118px;
    line-height: 1;
    letter-spacing: 0.01em;
  }
  .title-line .initial { font-size: 158px; }
  .title-number {
    top: 215px;
    font-family: "Cormorant Garamond", serif;
    font-weight: 500;
    font-size: 370px;
    line-height: 1;
    letter-spacing: -0.06em;
    font-variant-numeric: oldstyle-nums;
  }
  .title-tag {
    top: 614px;
    padding-left: 0.3em;
    font-family: "Cinzel", serif;
    font-weight: 500;
    font-size: 80px;
    line-height: 1;
    letter-spacing: 0.3em;
    text-shadow: 4px 4px 0 var(--ink-shadow);
  }
  .subtitle-lead {
    top: 912px;
    font-family: "Tinos", serif;
    font-size: 28px;
    line-height: 1;
    text-transform: uppercase;
  }
  .subtitle-body {
    top: 964px;
    font-family: "Tinos", serif;
    font-size: 26px;
    line-height: 35px;
  }
  .author {
    top: 1078px;
    padding-left: 0.4em;
    font-family: "Cinzel", serif;
    font-weight: 400;
    font-size: 52px;
    line-height: 1;
    letter-spacing: 0.4em;
  }
</style>
</head>
<body>
<main class="cover">
  <svg class="cover-art" viewBox="0 0 805 1200" role="img" aria-label="Cosmic background of layered glowing triangles in sacred geometry, violet and pink light on deep indigo space with scattered stars">
    <defs>
      <radialGradient id="core-glow" cx="50%" cy="48%" r="48%">
        <stop offset="0" stop-color="var(--glow-pink)" stop-opacity="0.85"/>
        <stop offset="0.35" stop-color="var(--glow-violet)" stop-opacity="0.7"/>
        <stop offset="0.75" stop-color="var(--space-indigo)" stop-opacity="0.6"/>
        <stop offset="1" stop-color="var(--space-deep)" stop-opacity="0"/>
      </radialGradient>
      <linearGradient id="space-fade" x1="0" y1="0" x2="0" y2="1">
        <stop offset="0" stop-color="#1c1850"/>
        <stop offset="0.5" stop-color="#241c5c"/>
        <stop offset="1" stop-color="var(--space-deep)"/>
      </linearGradient>
    </defs>
    <rect width="805" height="1200" fill="url(#space-fade)"/>
    <rect width="805" height="1200" fill="url(#core-glow)"/>
  </svg>

  <h1 class="book-title">
    <span class="title-line"><span class="initial">V</span>ENTURE</span>
    <span class="title-number">482</span>
    <span class="title-tag">ASCENDED</span>
  </h1>

  <p class="subtitle-lead">Shaping Outcomes:</p>
  <p class="subtitle-body">Paths to unlocking<br>cosmic truths</p>

  <p class="author">DORIAN PELL</p>
</main>
</body>
</html>
```